The Lantern Guild Pitchdeck Template

The Lantern Guild would like a branded pitch deck template design for members to use when presenting their projects and proposals. The deck should include 10-15 different slide designs, each with the same branded theme, but with a variety of icon graphics and other design features that will empower members to easily create a beautiful pitch deck just by adding written content.

Please visit lanternguildhq.org to get a sense for our branding - purple, space, galaxy, white font and the planetary logo are some commonalities.

Here are 2 google drive links with some additional designs

https://files.boxmeadow.net/share/f/8QzrTa2Lk5VbNw7cHyP0dJe3sUmXg4RiF

https://files.boxmeadow.net/share/f/3Kd9-Rm6Tq2-yLvBn051fopwxhcT_zj7

```html
<!DOCTYPE html>
<html lang="en">
<head>
<meta charset="utf-8">
<title>The Lantern Guild – Pitch Deck Template</title>
<link rel="stylesheet" href="https://fonts.googleapis.com/css2?family=Jost:wght@400;500;600&family=Lato:wght@400;700&display=swap">
<style>
  :root {
    --canvas: #878787;
    --white: #ffffff;
    --ink: #111111;
    --body: #6f6f6f;
    --violet: #3d0a9c;
    --violet-deep: #2a0678;
    --magenta: #9b1fb8;
    --pink: #d85ad6;
    --lilac: #ece4f7;
  }
  * { box-sizing: border-box; margin: 0; padding: 0; }
  html, body { width: 1200px; height: 3846px; overflow: hidden; }
  body { background: var(--canvas); position: relative; font-family: "Lato", sans-serif; }

  .slide { position: absolute; left: 112px; width: 978px; height: 550px; overflow: hidden; background: var(--white); }
  .slide--cover { top: 104px; }
  .slide--about { top: 718px; }
  .slide--vision { top: 1336px; }
  .slide--intent { top: 1958px; }
  .slide--support { top: 2572px; }
  .slide--thanks { top: 3190px; }

  .abs { position: absolute; }
  .brand { position: absolute; font-family: "Jost", sans-serif; font-weight: 600; letter-spacing: 3px; line-height: 1; }
  .brand__name { display: block; font-size: 26px; }
  .brand__sub { display: block; font-size: 10px; letter-spacing: 0.6px; margin-top: 4px; font-weight: 500; }
  .brand--dark { right: 22px; top: 16px; color: var(--ink); text-align: left; }
  .brand--dark .brand__sub { color: var(--magenta); }

  .eyebrow { font-family: "Jost", sans-serif; font-size: 17px; color: var(--magenta); letter-spacing: 0.3px; white-space: nowrap; }
  .heading { font-family: "Jost", sans-serif; font-weight: 500; font-size: 36px; letter-spacing: 1.5px; color: var(--ink); line-height: 1.1; white-space: nowrap; }
  .heading--vision { font-size: 33px; letter-spacing: 1px; }
  .copy { font-size: 11px; line-height: 20.5px; color: var(--body); }

  /* Cover */
  .cover__photo { position: absolute; inset: 0; background: radial-gradient(ellipse at 72% 30%, #a48cff 0%, #5a2ee0 25%, transparent 55%), radial-gradient(ellipse at 88% 85%, #1c0a55 0%, transparent 45%), linear-gradient(120deg, #4a18d6 0%, #3b0fb8 55%, #22087a 100%); }
  .cover .brand { left: 37px; top: 18px; color: var(--white); }
  .cover__kicker { left: 34px; top: 196px; font-family: "Jost", sans-serif; font-size: 21px; color: var(--white); letter-spacing: 1px; }
  .cover__title { left: 34px; top: 227px; font-family: "Jost", sans-serif; font-weight: 500; font-size: 39px; color: var(--white); letter-spacing: 1.5px; white-space: nowrap; }
  .cover__copy { left: 36px; top: 290px; width: 440px; font-size: 11.5px; line-height: 20.5px; color: var(--white); }

  /* About */
  .strip { position: absolute; top: 0; width: 84px; border-radius: 0 0 42px 42px; background: linear-gradient(180deg, #c8a0e6 0%, #8a3fb0 40%, #6c2a98 70%, #b43fb8 100%); }

  /* Vision */
  .vision__photo { position: absolute; top: 73px; width: 172px; height: 262px; border-radius: 4px; }
  .vision__photo--people { left: 27px; background: linear-gradient(180deg, #8a78d8 0%, #6b4cb8 50%, #3d6b2a 100%); }
  .vision__photo--planet { left: 218px; background: radial-gradient(ellipse at 50% 50%, #e8b8e8 0%, #7a3aa0 20%, #120a2e 55%, #070616 100%); }
  .vision__photo--peace { left: 407px; background: linear-gradient(180deg, #6a2a10 0%, #d8621a 45%, #f8b020 75%, #f0d040 100%); }
  .vision__card { position: absolute; background: var(--white); border-radius: 6px; box-shadow: 0 2px 8px rgba(0,0,0,0.14); text-align: center; padding: 12px 12px; }
  .vision__card h3 { font-family: "Jost", sans-serif; font-weight: 500; font-size: 16px; color: var(--ink); margin-bottom: 6px; }
  .vision__card p { font-size: 8.5px; line-height: 16px; color: var(--body); }
  .vision__card--people { left: 27px; top: 343px; width: 172px; height: 121px; }
  .vision__card--planet { left: 209px; top: 347px; width: 190px; height: 128px; background: var(--violet); }
  .vision__card--planet h3, .vision__card--planet p { color: var(--white); }
  .vision__card--peace { left: 407px; top: 347px; width: 172px; height: 121px; }

  /* Intentions */
  .intent__photo { position: absolute; left: 487px; top: 121px; width: 491px; height: 358px; border-radius: 180px 0 0 180px; background: radial-gradient(ellipse at 55% 25%, #f0a0b0 0%, #c85a8a 30%, transparent 60%), linear-gradient(180deg, #c04a7a 0%, #8a2a8a 55%, #4a1a8a 100%); }

  /* Support */
  .support .brand { right: 22px; top: 16px; color: var(--white); }
  .support__kicker { left: 0; right: 0; top: 96px; text-align: center; font-family: "Jost", sans-serif; font-size: 16px; color: #c640c8; letter-spacing: 0.5px; }
  .support__title { left: 0; right: 0; top: 132px; text-align: center; font-family: "Jost", sans-serif; font-weight: 500; font-size: 34px; color: var(--white); letter-spacing: 2px; }
  .pillar { position: absolute; width: 280px; text-align: center; }
  .pillar__badge { width: 110px; height: 110px; border-radius: 50%; margin: 0 auto; background: linear-gradient(135deg, #4a10b8 0%, #a21cc4 100%); display: flex; align-items: center; justify-content: center; }
  .pillar h3 { font-family: "Jost", sans-serif; font-weight: 500; font-size: 20px; letter-spacing: 1px; color: var(--ink); margin: 10px 0 8px; }
  .pillar p { font-size: 9.5px; line-height: 18px; color: var(--body); }
  .pillar--partner { left: 42px; top: 237px; }
  .pillar--contribute { left: 354px; top: 254px; }
  .pillar--member { left: 654px; top: 239px; }

  /* Thanks */
  .thanks__photo { position: absolute; left: 0; top: 0; width: 589px; height: 550px; background: radial-gradient(ellipse at 45% 30%, #e070d8 0%, #8a3ad0 25%, transparent 55%), linear-gradient(180deg, #2a0a6a 0%, #4a1aa8 45%, #2a0a70 100%); }
  .thanks__panel { position: absolute; left: 589px; top: 0; width: 389px; height: 248px; background: var(--violet); padding: 40px 36px 0 34px; color: var(--white); }
  .thanks__panel .brand__name { font-family: "Jost", sans-serif; font-weight: 600; font-size: 40px; letter-spacing: 5px; }
  .thanks__panel .brand__sub { font-family: "Jost", sans-serif; font-size: 16px; letter-spacing: 0.6px; margin-top: 6px; }
  .thanks__panel p { font-size: 10.5px; line-height: 18px; margin-top: 12px; }
  .thanks__label { left: 618px; top: 284px; font-family: "Jost", sans-serif; font-size: 13px; color: var(--violet); letter-spacing: 0.3px; }
  .thanks__title { left: 620px; top: 306px; font-family: "Jost", sans-serif; font-weight: 500; font-size: 34px; letter-spacing: 1px; color: var(--ink); white-space: nowrap; }
  .contact { position: absolute; left: 632px; width: 320px; display: flex; gap: 12px; font-size: 14px; line-height: 20px; color: var(--ink); }
  .contact svg { flex: none; width: 16px; height: 16px; margin-top: 2px; fill: var(--violet); }
</style>
</head>
<body>

<section class="slide slide--cover cover">
  <div class="cover__photo" role="img" aria-label="Purple galaxy sky above a lone figure standing on a rocky peak"></div>
  <div class="brand"><span class="brand__name">LUMEN</span><span class="brand__sub">LANTERN GUILD</span></div>
  <div class="abs cover__kicker">WELCOME TO LUMEN</div>
  <h1 class="abs cover__title">LANTERN GUILD</h1>
  <p class="abs cover__copy">Lorem ipsum dolor sit amet, consectetur adipiscing elit, sed do eiusmod tempor incididunt ut labore et dolore magna aliqua. Quis ipsum suspendisse ultrices gravida. Risus commodo viverra maecenas accumsan lacus vel facilisis.</p>
</section>

<section class="slide slide--about">
  <div role="img" aria-label="Violet mountain and desert landscape seen through vertical rounded strips">
    <div class="strip" style="left:7px;height:331px"></div>
    <div class="strip" style="left:97px;height:509px"></div>
    <div class="strip" style="left:186px;height:428px"></div>
    <div class="strip" style="left:276px;height:376px"></div>
    <div class="strip" style="left:366px;height:313px"></div>
    <div class="strip" style="left:463px;height:263px"></div>
    <div class="strip" style="left:555px;height:201px"></div>
    <div class="strip" style="left:646px;height:163px"></div>
  </div>
  <div class="brand brand--dark"><span class="brand__name">LUMEN</span><span class="brand__sub">LANTERN GUILD</span></div>
  <div class="abs eyebrow" style="left:498px;top:306px">LOREM IPSUM</div>
  <h2 class="abs heading" style="left:498px;top:336px">WHO ARE WE</h2>
  <p class="abs copy" style="left:498px;top:394px;width:428px">The Lantern Guild is a spiritual, conscious and regenerative non-profit organisation established for furthering the upliftment, enlightenment, spiritual realisation, and general welfare of people throughout the world, the betterment of life on planet Earth, and other spiritual, environmental, humanitarian, and beneficent purpose. Buddhism, Christianity, Hinduism, Islam, Judaism and other religions are belief systems; The Universe exists whether you believe in it or not.</p>
</section>

<section class="slide slide--vision">
  <div class="vision__photo vision__photo--people" role="img" aria-label="Two children walking through a lavender field"></div>
  <div class="vision__photo vision__photo--planet" role="img" aria-label="Glowing black hole in deep space"></div>
  <div class="vision__photo vision__photo--peace" role="img" aria-label="Dove carrying an olive branch against a golden sunset"></div>
  <div class="vision__card vision__card--people"><h3>People</h3><p>A World that meets the needs of every human being as a birth right, providing the foundation for self-actualisation.</p></div>
  <div class="vision__card vision__card--planet"><h3>Planet</h3><p>A World that lives in harmony with Nature; restore and protect Mother Earth, including the Animal Kingdom.</p></div>
  <div class="vision__card vision__card--peace"><h3>Peace</h3><p>A World that chooses peace, love and harmony, awake and aware of its connection with everything.</p></div>
  <div class="brand brand--dark"><span class="brand__name">LUMEN</span><span class="brand__sub">LANTERN GUILD</span></div>
  <div class="abs eyebrow" style="left:601px;top:192px">LOREM IPSUM</div>
  <h2 class="abs heading heading--vision" style="left:601px;top:222px">WHAT WE ENVISION</h2>
  <p class="abs copy" style="left:602px;top:278px;width:350px">Lorem ipsum dolor sit amet, consectetur adipiscing elit, sed do eiusmod tempor incididunt ut labore et dolore magna aliqua.</p>
</section>

<section class="slide slide--intent">
  <div class="brand brand--dark"><span class="brand__name">LUMEN</span><span class="brand__sub">LANTERN GUILD</span></div>
  <div class="abs eyebrow" style="left:50px;top:100px">LOREM IPSUM</div>
  <h2 class="abs heading" style="left:50px;top:130px">INTENTIONS</h2>
  <p class="abs copy" style="left:52px;top:188px;width:412px">The Lantern Guild, members, missionaries, stewards, sponsors, partners, and donors are working on various initiatives to fulfil our intentions. As a collective we are focusing on every area; from education, healthcare, economics, finance, governance &amp; technology, to space travel, art, music and transformational experiences. Our mission is to protect the Spirit of Air, Water, Land and Food; to create a system that supports the people and the planet; to redistribute wealth; protect human rights; serve justice and implement the conscious economy. We are focused on building a global community, transforming local environments, integration with Indigenous tribes and the reformation of society. We are interested in new paradigm schools and Universities, incubators for regenerative technology, natural medicine, empowering micro-industries, entrepreneurs, investors, inventors, artists and creatives. If you are involved in any initiative that benefits the collective, we would love to support you.</p>
  <div class="intent__photo" role="img" aria-label="Pink alien shoreline with a ringed planet and glowing orbits above a lone walker"></div>
</section>

<section class="slide slide--support support">
  <svg class="abs" style="left:0;top:0" width="978" height="330" viewBox="0 0 978 330" role="img" aria-label="Dark cosmic scene with rocky cliffs, clouds and planets">
    <defs>
      <linearGradient id="spaceFill" x1="0" y1="0" x2="1" y2="1">
        <stop offset="0" stop-color="#0c1020"/>
        <stop offset="0.45" stop-color="#243a6a"/>
        <stop offset="0.75" stop-color="#1a1a3a"/>
        <stop offset="1" stop-color="#3a2a1a"/>
      </linearGradient>
    </defs>
    <path d="M0 0 H978 V257 Q600 340 420 316 Q180 285 0 227 Z" fill="url(#spaceFill)"/>
  </svg>
  <div class="brand"><span class="brand__name">LUMEN</span><span class="brand__sub">LANTERN GUILD</span></div>
  <div class="abs support__kicker">JOIN THE GUILD</div>
  <h2 class="abs support__title">SUPPORT THE GUILD</h2>

  <div class="pillar pillar--partner">
    <div class="pillar__badge">
      <svg width="54" height="54" viewBox="0 0 48 48" fill="none" stroke="#fff" stroke-width="2" stroke-linecap="round" stroke-linejoin="round"><path d="M4 20l8-8 8 4 6-4 6 2 12 10"/><path d="M14 26l8 8a3 3 0 004-4"/><path d="M20 30l6 6a3 3 0 004-4l-8-8"/><path d="M26 26l6 6a3 3 0 004-4l-10-10"/><path d="M4 20l8 8"/></svg>
    </div>
    <h3>Partner</h3>
    <p>We are stronger together. If you are a conscious and regenerative project or organisation doing good in the world, please apply to join the guild now, and benefit from a network of resources, knowledge and expertise including funding, technical support, legal, tax and accounting, marketing, operational expense reduction, story telling and movement building.</p>
  </div>

  <div class="pillar pillar--contribute">
    <div class="pillar__badge">
      <svg width="54" height="54" viewBox="0 0 48 48" fill="none" stroke="#fff" stroke-width="2" stroke-linejoin="round"><path d="M8 8h12v4a3 3 0 006 0V8h12v12h-4a3 3 0 000 6h4v12H26v-4a3 3 0 00-6 0v4H8V26h4a3 3 0 000-6H8z"/></svg>
    </div>
    <h3>Contribute</h3>
    <p>Take action by contributing your time, love and energy. Explore the Guild, its projects, and all partner organisations in the DHO, a Decentralised Human Organisation. Discover paid roles, quests, and opportunities available across the globe within our ever expanding community. Create a role for yourself, or even start a project of your own.</p>
  </div>

  <div class="pillar pillar--member">
    <div class="pillar__badge">
      <svg width="54" height="54" viewBox="0 0 48 48" fill="none" stroke="#fff" stroke-width="2" stroke-linecap="round"><circle cx="24" cy="12" r="4"/><circle cx="12" cy="16" r="3.5"/><circle cx="36" cy="16" r="3.5"/><path d="M16 30a8 8 0 0116 0"/><path d="M5 30a7 7 0 0111-5"/><path d="M43 30a7 7 0 00-11-5"/><circle cx="24" cy="36" r="6"/><path d="M24 33l1 2h2l-1.5 1.5.5 2-2-1-2 1 .5-2L21 35h2z"/></svg>
    </div>
    <h3>Membership</h3>
    <p>The Law of Personal Return states that giving is receiving! In accordance with this Universal Law, The Guild gives back to its Members. Tax-deductible donations are used to fund conscious and regenerative projects and organisations that create a positive impact on the people and the planet, as well as wealth for The Guild and Members.</p>
  </div>
</section>

<section class="slide slide--thanks">
  <div class="thanks__photo" role="img" aria-label="Violet nebula sky over a large tree silhouette"></div>
  <div class="thanks__panel">
    <span class="brand__name">LUMEN</span>
    <span class="brand__sub">LANTERN GUILD</span>
    <p>Lorem ipsum dolor sit amet, consectetur adipiscing elit, sed do eiusmod tempor incididunt ut labore et dolore magna aliqua. Quis ipsum suspendisse ultrices gravida. Risus commodo viverra maecenas accumsan lacus vel facilisis. Lorem ipsum dolor sit amet, consectetur adipiscing elit, sed do eiusmod</p>
  </div>
  <div class="abs thanks__label">LANTERN GUILD</div>
  <h2 class="abs thanks__title">THANK YOU</h2>
  <div class="contact" style="top:361px">
    <svg viewBox="0 0 24 24"><path d="M12 2a7 7 0 00-7 7c0 5 7 13 7 13s7-8 7-13a7 7 0 00-7-7zm0 9.5A2.5 2.5 0 1112 6.5a2.5 2.5 0 010 5z"/></svg>
    <span>Lorem ipsum dolor sit amet,<br>consectetur</span>
  </div>
  <div class="contact" style="top:414px">
    <svg viewBox="0 0 24 24"><path d="M6.6 10.8a15 15 0 006.6 6.6l2.2-2.2a1 1 0 011-.25 11.4 11.4 0 003.6.6 1 1 0 011 1V20a1 1 0 01-1 1A17 17 0 013 4a1 1 0 011-1h3.5a1 1 0 011 1 11.4 11.4 0 00.6 3.6 1 1 0 01-.25 1z"/></svg>
    <span>+1 888 888 8888</span>
  </div>
  <div class="contact" style="top:455px">
    <svg viewBox="0 0 24 24"><path d="M12 2a10 10 0 100 20 10 10 0 000-20zm6.9 6h-2.9a15.7 15.7 0 00-1.4-3.6A8 8 0 0118.9 8zM12 4a14 14 0 011.9 4h-3.8A14 14 0 0112 4zM4.3 14a8.2 8.2 0 010-4h3.4a16.5 16.5 0 000 4zm.8 2h2.9a15.7 15.7 0 001.4 3.6A8 8 0 015.1 16zM8 8H5.1a8 8 0 014.3-3.6A15.7 15.7 0 008 8zm4 12a14 14 0 01-1.9-4h3.8A14 14 0 0112 20zm2.3-6H9.7a14.7 14.7 0 010-4h4.6a14.7 14.7 0 010 4zm.3 5.6a15.7 15.7 0 001.4-3.6h2.9a8 8 0 01-4.3 3.6zm1.7-5.6a16.5 16.5 0 000-4h3.4a8.2 8.2 0 010 4z"/></svg>
    <span>www.lanternguildhq.org</span>
  </div>
  <div class="contact" style="top:496px">
    <svg viewBox="0 0 24 24"><path d="M3 5h18a1 1 0 011 1v12a1 1 0 01-1 1H3a1 1 0 01-1-1V6a1 1 0 011-1zm9 7l8-5H4z"/></svg>
    <span>iam@lanternguildhq.org</span>
  </div>
</section>

</body>
</html>
```